Voltaryn - Web Design Project

I am looking for a 5 page design.
I would like it to be like the design of this site: www.quorvexlabs.com.
Which means it can be all one page effectively. With quick scroll tabs at the top.
I would like it to include parallax scrolling (The parallax effect uses multiple backgrounds which seem to move at different speeds to create a sensation of depth (creating a faux-3D effect)).
I have uploaded my logo. I would like this to be used in the site design.
I would like the site design to include 3D DNA creative.
Please note the Pixmora photos attached do not belong to me they are purely to inspire creative ideas. However I would be more than happy to purchase these photos to use if the designer thought this would be beneficial.
Requirements
Must have
- parallax scrolling
DNA pictures (3D effect)
Please use site for reference: www.quorvexlabs.com
Use at least 1 of the logos in design...

```html
<!DOCTYPE html>
<html lang="en">
<head>
<meta charset="utf-8">
<title>Voltaryn – Hybrid Advertising</title>
<link href="https://fonts.googleapis.com/css2?family=Archivo+Black&family=Arimo:wght@400;700&display=swap" rel="stylesheet">
<style>
:root{
  --ink:#3c3c3c;
  --white:#ffffff;
  --sky:#9ccbf0;
  --navy:#0b2f55;
  --steel:#4f83b4;
  --grey-head:#8a8a8a;
  --orange:#f2913c;
  --orange-deep:#f07f1e;
  --red:#a8060b;
  --red-deep:#6d0206;
  --nav-teal:#3fa8cf;
  --footer:#4a4a4a;
  --footer-text:#c9c9c9;
}
*{margin:0;padding:0;box-sizing:border-box}
html,body{width:1200px;height:2795px;overflow:hidden}
body{position:relative;font-family:"Arimo",Arial,sans-serif;color:var(--ink);background:var(--white)}
.abs{position:absolute}
.display{font-family:"Archivo Black","Arial Black",sans-serif;line-height:1;white-space:nowrap}
.copy{font-size:10.5px;line-height:16px}

/* header */
.site-header{top:0;left:0;width:1200px;height:90px;background:var(--white)}
.brand{left:178px;top:30px;display:flex;align-items:center;gap:8px;font-family:"Arimo",sans-serif;font-weight:700;font-size:17px;letter-spacing:2px;color:#2c5c8a}
.brand-dot{width:14px;height:14px;border-radius:50%;background:#2c5c8a}
.main-nav{top:34px;left:496px;display:flex;align-items:center;font-size:10px;color:#707070;letter-spacing:.3px}
.main-nav span{display:block;text-align:center}
.main-nav .is-active{width:65px;height:24px;line-height:24px;background:linear-gradient(#6cc4e4,var(--nav-teal));color:var(--white);border-radius:2px;box-shadow:0 1px 2px rgba(0,0,0,.3)}
.main-nav .link{width:112px}

/* hero */
.hero{top:90px;left:0;width:1200px;height:482px;background:radial-gradient(ellipse at 78% 35%,#3a78b8 0%,#164777 35%,var(--navy) 75%)}
.hero-visual{left:615px;top:10px;width:430px;height:440px;border-radius:50%;background:radial-gradient(circle at 50% 45%,rgba(190,225,255,.75),rgba(90,150,210,.35) 45%,rgba(20,70,120,0) 70%)}
.hero-title-a{left:180px;top:138px;font-size:62px;color:var(--sky)}
.hero-title-b{left:180px;top:210px;font-size:64px;color:var(--white)}
.hero-title-b small{font-size:33px}
.hero-sub{left:180px;top:295px;font-size:27px;color:var(--white)}
.hero-copy{left:181px;top:332px;width:460px;color:var(--white);font-size:9.5px;line-height:15px}
.slider-dots{left:978px;top:461px;display:flex;gap:4px}
.slider-dots i{width:9px;height:9px;border-radius:50%;background:#8aa3bd}
.slider-dots i:first-child{background:#c5d3e2}

/* panels */
.panel{left:0;width:1200px;height:540px;overflow:hidden}
.to-top{font-size:9px;text-align:center;width:30px;line-height:1}
.to-top svg{display:block;margin:0 auto 2px}

.about{top:572px;background:linear-gradient(90deg,#f2f4f6,#fff 60%)}
.about-visual{left:0;top:0;width:560px;height:540px;background:radial-gradient(ellipse at 45% 55%,#6e8aa8 0%,#a9bccf 35%,rgba(240,243,246,0) 70%)}
.about-title-a{left:600px;top:76px;font-size:52px;color:var(--grey-head)}
.about-title-b{left:602px;top:128px;font-size:62px;color:var(--sky)}
.about-lead{left:604px;top:214px;width:410px;color:#333}
.about-col{left:604px;top:268px;width:210px;color:#333}
.about-col p+p{margin-top:16px}
.about-photo{left:840px;top:263px;width:175px;height:201px;background:linear-gradient(135deg,#e7d7b0,#c87a2a 55%,#8e4a16);border:3px solid #fff;box-shadow:0 0 3px rgba(0,0,0,.35)}

.services{top:1112px;background:linear-gradient(90deg,#0f3c6a 0%,#2b6399 40%,#4f83b4 60%,#5788b7 100%)}
.services-visual{left:0;top:0;width:620px;height:540px;background:radial-gradient(ellipse at 40% 50%,rgba(160,210,250,.55),rgba(60,120,180,.2) 45%,rgba(15,60,106,0) 75%)}
.services-title-a{left:643px;top:143px;font-size:45px;color:var(--sky)}
.services-title-b{left:643px;top:190px;font-size:63px;color:var(--white)}
.services-copy{left:650px;top:264px;width:370px;color:var(--white)}
.services-copy p+p{margin-top:16px}

.research{top:1652px;background:linear-gradient(90deg,var(--orange) 0%,#f39444 42%,#f7e9dc 62%,#f5f5f5 75%)}
.research-visual{left:560px;top:0;width:640px;height:540px;background:radial-gradient(ellipse at 55% 55%,rgba(212,140,40,.75),rgba(235,180,90,.4) 40%,rgba(245,245,245,0) 72%)}
.research-title-a{left:182px;top:122px;font-size:45px;color:var(--white)}
.research-title-b{left:182px;top:168px;font-size:63px;color:var(--white)}
.research-copy{left:190px;top:243px;width:375px;color:var(--white)}
.research-copy p+p{margin-top:16px}

.contact{top:2193px;background:radial-gradient(ellipse at 50% 40%,#c3100f 0%,var(--red) 45%,var(--red-deep) 100%)}
.contact-visual{left:0;top:0;width:1200px;height:540px;background:radial-gradient(circle at 12% 25%,rgba(230,60,60,.45),rgba(0,0,0,0) 18%),radial-gradient(circle at 72% 15%,rgba(230,60,60,.45),rgba(0,0,0,0) 16%),radial-gradient(circle at 90% 70%,rgba(230,60,60,.35),rgba(0,0,0,0) 18%)}
.contact-title-a{left:199px;top:153px;font-size:45px;color:var(--orange-deep)}
.contact-title-b{left:199px;top:198px;font-size:63px;color:var(--white)}
.contact-copy{left:207px;top:270px;width:395px;color:var(--white)}
.contact-map{left:209px;top:316px;width:219px;height:136px;background:linear-gradient(135deg,#e9e6dc,#d7d3c5);border:4px solid #fff}
.contact-card{left:453px;top:322px;color:var(--white);font-size:11px;line-height:16px}
.contact-card strong{display:block;font-size:17px;font-weight:400;margin-bottom:6px}
.contact-divider{left:619px;top:255px;width:1px;height:170px;background:rgba(255,255,255,.5)}
.quote-title{left:645px;top:272px;font-family:"Arimo",sans-serif;font-weight:700;font-size:19px;color:var(--white);letter-spacing:.5px}
.field{background:var(--white);border-radius:2px;font-size:9px;color:#888;padding:4px 8px}
.f-name{left:645px;top:320px;width:167px;height:19px}
.f-email{left:825px;top:320px;width:168px;height:19px}
.f-phone{left:645px;top:352px;width:167px;height:19px}
.f-message{left:825px;top:352px;width:168px;height:54px}
.submit{left:918px;top:421px;width:75px;height:17px;border-radius:3px;background:linear-gradient(#e6e6e6,#9c9c9c);font-size:9px;font-weight:700;color:#333;text-align:center;line-height:17px}

.to-top.light{color:var(--white)}
.to-top.dim{color:#5a7ea8}
.to-top.orange{color:var(--orange-deep)}

/* footer */
.site-footer{top:2733px;left:0;width:1200px;height:62px;background:var(--footer);color:var(--footer-text);font-size:9.5px}
.footer-nav{left:194px;top:16px;display:flex;gap:0}
.footer-nav span{margin-right:22px}
.footer-nav b{font-weight:400;margin-right:22px}
.footer-copy{left:194px;top:31px}
.follow{left:857px;top:22px;display:flex;align-items:center;gap:10px}
.social{width:26px;height:26px;border-radius:50%;background:#2a6aa8}
.social.alt{background:#2ba9e1}
.social.pro{background:#1f79b8}
</style>
</head>
<body>

<header class="site-header abs">
  <div class="brand abs"><span class="brand-dot"></span>VOLTARYN</div>
  <nav class="main-nav abs">
    <span class="is-active">HOME</span>
    <span class="link">ABOUT US</span>
    <span class="link">SERVICES</span>
    <span class="link">RESEARCH</span>
    <span class="link">CONTACT</span>
  </nav>
</header>

<section class="hero abs">
  <div class="hero-visual abs" role="img" aria-label="Glowing blue 3D head with a brain and orbiting light rings"></div>
  <div class="hero-title-a display abs">Voltaryn</div>
  <div class="hero-title-b display abs">Hybrid <small>Advertising</small></div>
  <div class="hero-sub display abs">its a DNA research</div>
  <p class="hero-copy abs">Lorem Ipsum is simply dummy text of the printing and typesetting industry. Lorem Ipsum has been the industry's standard dummy text ever since the 1500s, when an unknown printer took a galley of type and scrambled it to make a type specimen book. It has survived not only five centuries.</p>
  <div class="slider-dots abs"><i></i><i></i><i></i></div>
</section>

<section class="panel about abs">
  <div class="about-visual abs" role="img" aria-label="3D metallic DNA double helix twisting across the panel"></div>
  <div class="about-title-a display abs">About</div>
  <div class="about-title-b display abs">Voltaryn</div>
  <p class="about-lead copy abs">Lorem Ipsum is simply dummy text of the printing and typesetting industry. Lorem Ipsum has been the industry's standard dummy text ever since the 1500s.</p>
  <div class="about-col copy abs">
    <p>Lorem Ipsum is simply dummy text of the printing and typesetting industry. Lorem Ipsum has been the industry's standard dummy text ever since the 1500s, when an unknown printer took a galley of type and scrambled it to make a type specimen book. It has survived not only five centuries, but also the leap into electronic typesetting, remaining essentially unchanged.</p>
    <p>Lorem Ipsum is simply dummy text of the printing and typesetting industry. Lorem Ipsum has been the industry's standard dummy text ever since the 1500s, when an unknown printer took a galley of type and scrambled.</p>
  </div>
  <div class="about-photo abs" role="img" aria-label="Photo of a scientist examining an amber liquid in a lab flask"></div>
  <div class="to-top dim abs" style="left:1058px;top:505px">
    <svg width="8" height="10" viewBox="0 0 8 10"><path d="M4 10V1M1 4l3-3 3 3" fill="none" stroke="currentColor" stroke-width="1"/></svg>TOP</div>
</section>

<section class="panel services abs">
  <div class="services-visual abs" role="img" aria-label="X-ray style running figure with a glowing heartbeat line on a blue grid"></div>
  <div class="services-title-a display abs">Voltaryn</div>
  <div class="services-title-b display abs">Services</div>
  <div class="services-copy copy abs">
    <p>Lorem Ipsum is simply dummy text of the printing and typesetting industry. Lorem Ipsum has been the industry's standard dummy text ever since the 1500s, when an unknown printer took a galley of type and scrambled it to make a type specimen book. It has survived not only five centuries.Lorem Ipsum is simply dummy text of the printing and typesetting industry. Lorem Ipsum has been the industry's standard dummy text ever since the 1500s, when an unknown printer took a galley of type and scrambled it to make a type specimen book. It has survived not only five centuries.</p>
    <p>Lorem Ipsum is simply dummy text of the printing and typesetting industry. Lorem Ipsum has been the industry's standard dummy text ever since the 1500s, when an unknown printer took a galley of type and scrambled it to make a type specimen book. It has survived not only five centuries.</p>
  </div>
  <div class="to-top light abs" style="left:1058px;top:505px">
    <svg width="8" height="10" viewBox="0 0 8 10"><path d="M4 10V1M1 4l3-3 3 3" fill="none" stroke="currentColor" stroke-width="1"/></svg>TOP</div>
</section>

<section class="panel research abs">
  <div class="research-visual abs" role="img" aria-label="3D golden DNA strand with glossy orange spheres rising diagonally"></div>
  <div class="research-title-a display abs">Voltaryn</div>
  <div class="research-title-b display abs">Research</div>
  <div class="research-copy copy abs">
    <p>Lorem Ipsum is simply dummy text of the printing and typesetting industry. Lorem Ipsum has been the industry's standard dummy text ever since the 1500s, when an unknown printer took a galley of type and scrambled it to make a type specimen book. It has survived not only five centuries.Lorem Ipsum is simply dummy text of the printing and typesetting industry. Lorem Ipsum has been the industry's standard dummy text ever since the 1500s, when an unknown printer took a galley of type and scrambled it to make a type specimen book. It has survived not only five centuries.</p>
    <p>Lorem Ipsum is simply dummy text of the printing and typesetting industry. Lorem Ipsum has been the industry's standard dummy text ever since the 1500s, when an unknown printer took a galley of type and scrambled it to make a type specimen book. It has survived not only five centuries.</p>
  </div>
  <div class="to-top orange abs" style="left:1058px;top:505px">
    <svg width="8" height="10" viewBox="0 0 8 10"><path d="M4 10V1M1 4l3-3 3 3" fill="none" stroke="currentColor" stroke-width="1"/></svg>TOP</div>
</section>

<section class="panel contact abs">
  <div class="contact-visual abs" role="img" aria-label="Floating red blood cells on a deep red background"></div>
  <div class="contact-title-a display abs">Voltaryn</div>
  <div class="contact-title-b display abs">Contact</div>
  <p class="contact-copy copy abs">Lorem Ipsum is simply dummy text of the printing and typesetting industry. Lorem Ipsum has been the industry's standard dummy</p>
  <div class="contact-map abs" role="img" aria-label="Street map showing the office location"></div>
  <div class="contact-card abs">
    <strong>Voltaryn</strong>
    ( 11/111 (Area Name)<br>
    City Name<br>
    Zip code : 111111111<br>
    Phone : (0142) 555 018<br>
    Email : info@voltaryn.com
  </div>
  <div class="contact-divider abs"></div>
  <div class="quote-title abs">Requst a Quote :</div>
  <div class="field f-name abs">Name :</div>
  <div class="field f-email abs">Email :</div>
  <div class="field f-phone abs">Phone :</div>
  <div class="field f-message abs">Message :</div>
  <div class="submit abs">Submit</div>
  <div class="to-top light abs" style="left:1058px;top:505px">
    <svg width="8" height="10" viewBox="0 0 8 10"><path d="M4 10V1M1 4l3-3 3 3" fill="none" stroke="currentColor" stroke-width="1"/></svg>TOP</div>
</section>

<footer class="site-footer abs">
  <div class="footer-nav abs">
    <span>Home</span><b>|</b><span>About Us</span><b>|</b><span>Services</span><b>|</b><span>Research</span><b>|</b><span>Contact</span>
  </div>
  <div class="footer-copy abs">© 2013 Voltaryn. All Rights Reserved.</div>
  <div class="follow abs">
    <span>Follow Us :</span>
    <span class="social"></span>
    <span class="social alt"></span>
    <span class="social pro"></span>
  </div>
</footer>

</body>
</html>
```